Business Card Design for Marketing Firm

Looking for business card design for higher end marketing firm. Clean but impressionable/trendy. We are a marketing firm that represents manufacturers in the foodservice equipment and supply industry. Our customers are end users such has hotels, restaurants, country clubs, convention centers and casinos as well as distributors of restaurants supplies and equipment, and manufacturers of foodservice equipment and supplies.
Target Market(s)
Hotels, Restaurants, Supply & Equipment Distributors, Foodservice Manufacturers
Industry/Entity Type
Foodservice/Hospitality
Contact Information for Business Card
Name, Title, Contact Number, Email, Website, Social Media, Address
Requirements
Must have
- Clean & Simple but Serious and Impressionable

```html
<!DOCTYPE html>
<html lang="en">
<head>
<meta charset="UTF-8">
<title>Meridian Hospitality Reps – Business Card</title>
<link href="https://fonts.googleapis.com/css2?family=Montserrat:wght@400;500;600&display=swap" rel="stylesheet">
<style>
  :root {
    --backdrop: #e9e6e1;
    --card-white: #ffffff;
    --card-silver: #a9a9ab;
    --silver-text: #d9d9db;
    --navy: #2d2a6e;
    --ink: #2b2b3a;
    --muted: #55556a;
    --rule: #2d2a6e;
  }
  * { box-sizing: border-box; margin: 0; padding: 0; }
  html, body { width: 900px; height: 1200px; overflow: hidden; }
  body {
    background: var(--backdrop);
    font-family: "Montserrat", sans-serif;
    position: relative;
  }
  .card {
    position: absolute;
    left: 75px;
    width: 750px;
    height: 522px;
    border-radius: 34px;
    overflow: hidden;
    box-shadow: 0 10px 24px rgba(0,0,0,0.18);
  }
  .card-front { top: 66px; background: var(--card-white); }
  .card-back { top: 636px; background: var(--card-silver); }

  .brand {
    position: absolute;
    left: 40px;
    top: 150px;
    width: 360px;
    text-align: center;
    color: var(--navy);
    font-weight: 500;
    font-size: 28px;
    letter-spacing: 2px;
    line-height: 1.3;
    text-transform: uppercase;
  }
  .brand-mark {
    display: block;
    width: 22px; height: 22px;
    border-radius: 50%;
    background: var(--navy);
    margin: 0 auto 14px;
  }
  .brand-sub { font-size: 18px; letter-spacing: 6px; display: block; }

  .divider {
    position: absolute;
    left: 414px;
    top: 112px;
    width: 3px;
    height: 200px;
    background: var(--rule);
  }
  .contact {
    position: absolute;
    left: 438px;
    top: 112px;
    color: var(--ink);
  }
  .person-name { font-size: 28px; font-weight: 600; color: var(--navy); }
  .person-title { font-size: 16px; color: var(--muted); margin-top: 4px; }
  .contact-list { list-style: none; margin-top: 22px; }
  .contact-list li {
    display: flex; align-items: center; gap: 12px;
    font-size: 16px; color: var(--muted); margin-bottom: 9px;
  }
  .contact-list svg { width: 16px; height: 16px; fill: var(--navy); flex: none; }

  .address-band {
    position: absolute;
    left: 0; right: 0;
    top: 425px;
    height: 52px;
    background: var(--navy);
    color: #ffffff;
    font-size: 16px;
    display: flex; align-items: center; justify-content: center;
  }

  .back-brand {
    position: absolute;
    left: 0; right: 0;
    top: 170px;
    text-align: center;
    color: var(--silver-text);
    font-weight: 500;
    font-size: 52px;
    letter-spacing: 3px;
    line-height: 1.25;
    text-transform: uppercase;
  }
  .back-brand .brand-sub { font-size: 30px; letter-spacing: 10px; }
</style>
</head>
<body>
  <section class="card card-front">
    <div class="brand">
      <span class="brand-mark"></span>
      Meridian Hospitality
      <span class="brand-sub">Reps</span>
    </div>
    <div class="divider"></div>
    <div class="contact">
      <p class="person-name">Daniel Reyes</p>
      <p class="person-title">CEO &amp; Founder</p>
      <ul class="contact-list">
        <li>
          <svg viewBox="0 0 24 24"><path d="M6.6 10.8a15 15 0 0 0 6.6 6.6l2.2-2.2a1 1 0 0 1 1-.25 11.4 11.4 0 0 0 3.6.57 1 1 0 0 1 1 1V20a1 1 0 0 1-1 1A17 17 0 0 1 3 4a1 1 0 0 1 1-1h3.5a1 1 0 0 1 1 1c0 1.25.2 2.45.57 3.57a1 1 0 0 1-.25 1z"/></svg>
          (555) 214-0387
        </li>
        <li>
          <svg viewBox="0 0 24 24"><path d="M3 5h18a1 1 0 0 1 1 1v12a1 1 0 0 1-1 1H3a1 1 0 0 1-1-1V6a1 1 0 0 1 1-1zm9 7.2L4 7.5V9l8 4.7L20 9V7.5z"/></svg>
          info@meridianreps.com
        </li>
        <li>
          <svg viewBox="0 0 24 24"><path d="M12 2a10 10 0 1 0 0 20 10 10 0 0 0 0-20zm6.9 6h-2.9a15.6 15.6 0 0 0-1.4-3.6A8 8 0 0 1 18.9 8zM12 4a14 14 0 0 1 1.9 4h-3.8A14 14 0 0 1 12 4zM4.3 14a8 8 0 0 1 0-4h3.4a16 16 0 0 0 0 4zm.8 2h2.9a15.6 15.6 0 0 0 1.4 3.6A8 8 0 0 1 5.1 16zM8 8H5.1a8 8 0 0 1 4.3-3.6A15.6 15.6 0 0 0 8 8zm4 12a14 14 0 0 1-1.9-4h3.8A14 14 0 0 1 12 20zm2.3-6H9.7a14.6 14.6 0 0 1 0-4h4.6a14.6 14.6 0 0 1 0 4zm.3 5.6a15.6 15.6 0 0 0 1.4-3.6h2.9a8 8 0 0 1-4.3 3.6zm1.7-5.6a16 16 0 0 0 0-4h3.4a8 8 0 0 1 0 4z"/></svg>
          www.meridianreps.com
        </li>
      </ul>
    </div>
    <div class="address-band">420 Harbor Avenue, Suite 610, Portland, OR 97204</div>
  </section>

  <section class="card card-back">
    <div class="back-brand">
      Meridian Hospitality
      <span class="brand-sub">Reps</span>
    </div>
  </section>
</body>
</html>
```